Business Card Design Project

Doctor, Pain Management. Need a new business card design with appointment info on the back. New address is 18 Corvell Road, Suite 304, Brisdale, NJ 07391. Right now I believe the rest of the information is staying the same.

```html
<!DOCTYPE html>
<html lang="en">
<head>
<meta charset="utf-8">
<title>Calm Relief Clinic – Business Card</title>
<link href="https://fonts.googleapis.com/css2?family=Source+Sans+3:wght@400;600;700&display=swap" rel="stylesheet">
<style>
  :root {
    --page-bg: #1b1b1b;
    --card-dark: #232323;
    --card-light: #e4e4e4;
    --accent: #f26a1b;
    --text-light: #e6e6e6;
    --text-muted: #b4b4b4;
    --text-gray: #8d8d8d;
    --text-dark: #1e1e1e;
    --rule-dark: #4a4a4a;
    --rule-light: #a9a9a9;
  }
  * { box-sizing: border-box; margin: 0; padding: 0; }
  html, body { width: 1200px; height: 900px; overflow: hidden; }
  body {
    background: var(--page-bg);
    font-family: "Source Sans 3", Arial, sans-serif;
    position: relative;
  }
  .card {
    position: absolute;
    width: 525px;
    height: 300px;
    border-radius: 26px;
  }

  /* Back: appointment card */
  .card-back {
    left: 80px;
    top: 150px;
    background: var(--card-light);
    padding: 40px 44px 0;
  }
  .appointment-title {
    text-align: center;
    color: var(--accent);
    font-size: 22px;
    font-weight: 400;
    letter-spacing: 1px;
    margin-bottom: 26px;
  }
  .appointment-field {
    display: flex;
    align-items: flex-end;
    height: 46px;
    border-bottom: 1px solid var(--rule-light);
    color: var(--text-gray);
    font-size: 20px;
    padding-bottom: 4px;
  }
  .appointment-note {
    margin-top: 12px;
    font-size: 12.5px;
    color: var(--text-dark);
  }

  /* Front: doctor card */
  .card-front {
    left: 595px;
    top: 450px;
    background: var(--card-dark);
    color: var(--text-light);
  }
  .clinic-name {
    position: absolute;
    right: 34px;
    top: 24px;
    text-align: right;
    color: var(--accent);
    font-weight: 400;
    line-height: 1;
  }
  .clinic-name .line-main { display: block; font-size: 40px; }
  .clinic-name .line-sub { display: block; font-size: 24px; letter-spacing: 4px; margin-top: 6px; }
  .divider-top {
    position: absolute;
    right: 34px;
    top: 110px;
    width: 300px;
    height: 1px;
    background: var(--rule-dark);
  }
  .contact-list {
    position: absolute;
    right: 30px;
    top: 120px;
    list-style: none;
    text-align: right;
    font-size: 14px;
    line-height: 20px;
    color: var(--text-light);
  }
  .contact-list li { display: flex; justify-content: flex-end; align-items: center; gap: 6px; }
  .contact-list svg { width: 12px; height: 12px; fill: var(--accent); flex: none; }
  .doctor {
    position: absolute;
    left: 34px;
    top: 170px;
  }
  .doctor-name {
    color: var(--accent);
    font-size: 17px;
    line-height: 22px;
    font-weight: 700;
    letter-spacing: 0.3px;
  }
  .doctor-title {
    color: var(--text-muted);
    font-size: 14px;
    line-height: 18px;
    border-bottom: 1px solid var(--rule-dark);
    padding-bottom: 3px;
  }
  .address {
    position: absolute;
    left: 34px;
    bottom: 24px;
    font-size: 16px;
    line-height: 20px;
    color: var(--text-muted);
    font-style: normal;
  }
</style>
</head>
<body>

<section class="card card-back" aria-label="Appointment card, back">
  <h2 class="appointment-title">APPOINTMENT</h2>
  <div class="appointment-field">NAME:</div>
  <div class="appointment-field">DATE :</div>
  <div class="appointment-field">TIME :</div>
  <p class="appointment-note">If unable to keep your appointment,please contact us as soon as possible</p>
</section>

<section class="card card-front" aria-label="Business card, front">
  <h1 class="clinic-name">
    <span class="line-main">Calm Relief</span>
    <span class="line-sub">CLINIC</span>
  </h1>
  <div class="divider-top"></div>

  <ul class="contact-list">
    <li>555.204.3318
      <svg viewBox="0 0 12 12" aria-label="Phone"><path d="M2 1h2.5l1 3-1.5 1a6 6 0 0 0 3 3l1-1.5 3 1V10a1 1 0 0 1-1 1A9 9 0 0 1 1 2a1 1 0 0 1 1-1z"/></svg>
    </li>
    <li>555.204.3319
      <svg viewBox="0 0 12 12" aria-label="Fax"><rect x="3" y="1" width="6" height="3"/><rect x="1" y="4.5" width="10" height="5" rx="1"/><rect x="3" y="8" width="6" height="3"/></svg>
    </li>
    <li>www.calmreliefpm.com
      <svg viewBox="0 0 12 12" aria-label="Website"><circle cx="6" cy="6" r="5.5"/></svg>
    </li>
    <li>desk@calmreliefpm.com
      <svg viewBox="0 0 12 12" aria-label="Email"><rect x="0.5" y="2" width="11" height="8" rx="1"/></svg>
    </li>
  </ul>

  <div class="doctor">
    <p class="doctor-name">DR. WENLI HARROW, M.D., PH.D</p>
    <p class="doctor-title">Board Certified Anesthesiologist</p>
  </div>

  <address class="address">
    18 Corvell Road, Suite 304<br>
    Brisdale, NJ 07391
  </address>
</section>

</body>
</html>
```